Emerging automotive detailing business

I am starting a small automotive detailing business in hopes of becoming a well-known detailer to work on high end cars. I would like a card to reflect the high quality and time I put into my work. The name of the company is Bright Crest Detailing. I feel like it represents racecars getting off the line at the drag strip as well as an innuendo of "Up the Ladder". I do minor paint correction such as clay barring, multi-step buffing and polishing, waxing, hand washes, etc. I am always striving to learn more and improve my work. My goal is to have total customer satisfaction. This is a female run business but I do not want it to be very girly. Elegant is okay! I have pictures of my personal wrenfield attached, they do not need to be incorporated but if you can think of a cool way to use 1 or all of them, go for it!

Target Market(s)

Anyone that owns a vehicle. Preferably high end vehicles such as Valtori, Castellverde and Morvani but I will also happily work on any car, truck or suv no matter what brand.

Industry/Entity Type

Automotive

Contact Information for Business Card

Bright Crest Detailing
Mira Tolland
4175 Quenhollow Rd
Ashmere PA 17492
Cell phone- call/text- 717-555-0148
email- brightcrestdetails@maildrop-example.com
Instagram: @brightcrestdetailing
Facebook: facebook.com/brightcrestdetailing

Requirements
Must have
• Business name, my name, address, phone number. Listing that I do minor paint correction such as clay barring, multi-step buffing and polishing, waxing, hand washes, interior cleaning, and more. (This last part was in nice to haves but I have realized that I do really want it, so I moved it to must haves.) I want something that is different and eye-catching to my customers. Some people have done this very well with cards already submitted to me, but a lot have not. I didn't mess with the "look and feel bars" much because because I am pretty open to the overall design as long as it is not your basic run of the mill design.
Nice to have
• Something car related. Maybe an appointment time/date line. I do not have a logo, but if you would like to design one and incorporate it, that would be amazing!
Should not have
• Purple and Pink colors. Boring, basic, normal card.

```html
<!DOCTYPE html>
<html lang="en">
<head>
<meta charset="utf-8">
<title>Bright Crest Detailing – Business Card</title>
<link rel="stylesheet" href="https://fonts.googleapis.com/css2?family=Anton&family=Arimo:wght@400&family=Tinos:wght@400&display=swap">
<style>
  :root {
    --backdrop: #e9e6e1;
    --card: #fbfbfb;
    --card-band: #f2f2f2;
    --ink: #141414;
    --ink-soft: #6a6a6a;
    --rule: #1e1e1e;
    --dark-band: #3d3e40;
    --crease: #dcdcdc;
  }
  * { margin: 0; padding: 0; box-sizing: border-box; }
  html, body { width: 1200px; height: 892px; overflow: hidden; }
  body {
    background: var(--backdrop);
    display: flex;
    flex-direction: column;
    align-items: center;
    justify-content: center;
    gap: 40px;
    font-family: "Arimo", Arial, sans-serif;
    color: var(--ink);
  }
  .card {
    position: relative;
    width: 700px;
    height: 400px;
    background: var(--card);
    box-shadow: 0 2px 10px rgba(0,0,0,.15);
    overflow: hidden;
  }

  /* Contact side */
  .contact-side .name-band {
    position: absolute;
    left: 0; top: 0;
    width: 100%;
    height: 92px;
    background: var(--card-band);
    border-bottom: 1px solid var(--crease);
  }
  .contact-side .holder-name {
    position: absolute;
    left: 40px; top: 34px;
    font-size: 26px;
    font-weight: 400;
    color: var(--ink-soft);
    letter-spacing: .3px;
  }
  .contact-side .company {
    position: absolute;
    right: 70px; top: 128px;
    font-family: "Anton", Impact, sans-serif;
    font-weight: 400;
    font-size: 40px;
    letter-spacing: .3px;
    color: var(--ink);
  }
  .services {
    position: absolute;
    left: 40px; top: 178px;
    list-style: none;
    font-size: 15px;
    line-height: 24px;
    color: var(--ink-soft);
  }
  .services li::before {
    content: "";
    display: inline-block;
    width: 5px; height: 5px;
    margin: 0 9px 3px 0;
    background: var(--ink);
  }
  .contact-list {
    position: absolute;
    right: 30px; bottom: 30px;
    list-style: none;
    text-align: right;
  }
  .contact-list li {
    display: flex;
    justify-content: flex-end;
    align-items: center;
    gap: 10px;
    font-size: 19px;
    line-height: 30px;
  }
  .contact-list .email { font-size: 16px; }
  .icon-box {
    width: 16px; height: 16px;
    background: var(--ink);
    display: inline-flex;
    align-items: center;
    justify-content: center;
    flex: none;
  }
  .icon-box svg { width: 11px; height: 11px; }

  /* Name side */
  .name-side .dark-band {
    position: absolute;
    right: 0; top: 0;
    width: 92px; height: 100%;
    background: var(--dark-band);
  }
  .name-side .company {
    position: absolute;
    left: 0; right: 92px; top: 80px;
    text-align: center;
    font-family: "Tinos", "Times New Roman", serif;
    font-weight: 400;
    font-size: 40px;
    letter-spacing: .5px;
  }
  .name-side .holder-name {
    position: absolute;
    left: 0; right: 92px; top: 134px;
    text-align: center;
    font-size: 25px;
    letter-spacing: .5px;
  }
  .name-side .address-rule {
    position: absolute;
    left: 0; top: 252px;
    width: 608px; height: 40px;
  }
  .name-side .address {
    position: absolute;
    left: 48px; top: 300px;
    font-size: 21px;
    letter-spacing: .3px;
  }
</style>
</head>
<body>

  <section class="card contact-side" aria-label="Business card, contact side">
    <div class="name-band"></div>
    <p class="holder-name">Mira Tolland</p>
    <h1 class="company">Bright Crest Detailing</h1>
    <ul class="services" aria-label="Services">
      <li>Minor paint correction</li>
      <li>Clay barring</li>
      <li>Multi-step buffing &amp; polishing</li>
      <li>Waxing</li>
      <li>Hand washes</li>
      <li>Interior cleaning &amp; more</li>
    </ul>
    <ul class="contact-list">
      <li>717-555-0148
        <span class="icon-box"><svg viewBox="0 0 12 12"><path d="M3 1l2 2-1 1.5c.6 1.4 1.6 2.4 3 3L8.5 6.5l2 2L9 10.5C5 10 2 7 1.5 3z" fill="#fff"/></svg></span>
      </li>
      <li>@brightcrestdetailing <span class="icon-box"></span></li>
      <li class="email">brightcrestdetails@maildrop-example.com
        <span class="icon-box"><svg viewBox="0 0 12 12"><rect x="1.5" y="3" width="9" height="6" fill="none" stroke="#fff"/><path d="M1.5 3L6 6.5 10.5 3" fill="none" stroke="#fff"/></svg></span>
      </li>
      <li>4175 Quenhollow Rd,Ashmere PA 17492
        <span class="icon-box"><svg viewBox="0 0 12 12"><path d="M6 11S2.5 7 2.5 4.8a3.5 3.5 0 017 0C9.5 7 6 11 6 11z" fill="#fff"/><circle cx="6" cy="4.8" r="1.2" fill="#141414"/></svg></span>
      </li>
    </ul>
  </section>

  <section class="card name-side" aria-label="Business card, name side">
    <div class="dark-band"></div>
    <h2 class="company">Bright Crest Detailing</h2>
    <p class="holder-name">Mira Tolland</p>
    <svg class="address-rule" viewBox="0 0 608 40" aria-hidden="true">
      <line x1="0" y1="30" x2="608" y2="30" stroke="var(--rule)" stroke-width="2"/>
      <path d="M100 38s-11-12-11-20a11 11 0 0122 0c0 8-11 20-11 20z" fill="var(--card)" stroke="var(--rule)" stroke-width="3"/>
      <circle cx="100" cy="18" r="3.5" fill="var(--rule)"/>
    </svg>
    <p class="address">4175 Quenhollow Rd,Ashmere PA 17492</p>
  </section>

</body>
</html>
```